Verodex business card

Business card for sustainable investment company called "Verodex". Verodex is an exchange platform selling carbon credits between buyers and sellers. Carbon Credits are an environmental commodity for reducing global carbon emissions.

the card should obviously have our logo and the theme should be sustainability/environment mixed with a trading platform.

Contact Information for Business Card

Logo, Name, Title, Phone, Email

Colors
0054AA
0677BA
7BADD7
CADEEF
E8F1F8
0094D4
00A9DD
6FCCEA
C7EBF8
E9F6FB
00AB8E
00BBA5
67D7C9
C6EFE9
E9F9F6
59FF00
82FF00
B8FF75
E3FFCB
F4FFEA

```html
<!DOCTYPE html>
<html lang="en">
<head>
<meta charset="utf-8">
<title>Verodex business card</title>
<link rel="stylesheet" href="https://fonts.googleapis.com/css2?family=Montserrat:wght@700&family=Poppins:wght@400&family=Bebas+Neue&display=swap">
<style>
  :root {
    --stage: #1c1c1e;
    --card: #111112;
    --white: #ffffff;
    --blue: #2178ea;
    --cyan: #2fe3ee;
    --cyan-deep: #1fc8e6;
  }
  * { margin: 0; padding: 0; box-sizing: border-box; }
  html, body { width: 1200px; height: 900px; overflow: hidden; }
  body {
    background: var(--stage);
    display: flex;
    flex-direction: column;
    align-items: center;
    justify-content: center;
    gap: 40px;
  }
  .card {
    position: relative;
    width: 740px;
    height: 390px;
    background: var(--card);
    box-shadow: 0 10px 30px rgba(0,0,0,.6);
    overflow: hidden;
  }
  .card__band {
    position: absolute;
    left: 0; right: 0; bottom: 0;
    height: 14px;
  }
  .card--front .card__band { background: var(--blue); }
  .card--back .card__band { background: var(--cyan); }

  .brand {
    position: absolute;
    inset: 0 0 14px 0;
    display: flex;
    align-items: center;
    justify-content: center;
    gap: 22px;
  }
  .brand__mark {
    width: 54px; height: 54px;
    background: var(--cyan-deep);
  }
  .brand__name {
    font-family: "Montserrat", sans-serif;
    font-weight: 700;
    font-size: 72px;
    letter-spacing: 3px;
    color: var(--white);
    text-transform: uppercase;
  }

  .contact-layout {
    position: absolute;
    inset: 0 0 14px 0;
    display: flex;
    align-items: center;
    justify-content: center;
    gap: 30px;
  }
  .person { text-align: right; }
  .person__name {
    font-family: "Bebas Neue", sans-serif;
    font-size: 48px;
    line-height: 1;
    color: var(--cyan);
  }
  .person__surname { color: var(--blue); }
  .person__title {
    font-family: "Poppins", sans-serif;
    font-size: 19px;
    color: var(--white);
    margin-top: 2px;
  }
  .divider {
    width: 1.5px;
    height: 96px;
    background: var(--blue);
  }
  .details { list-style: none; }
  .details__item {
    display: flex;
    align-items: center;
    gap: 10px;
    font-family: "Poppins", sans-serif;
    font-size: 19px;
    line-height: 30px;
    color: var(--white);
  }
  .details__icon { width: 18px; height: 18px; flex: none; }
</style>
</head>
<body>
  <section class="card card--front">
    <div class="brand">
      <span class="brand__mark"></span>
      <span class="brand__name">Verodex</span>
    </div>
    <div class="card__band"></div>
  </section>

  <section class="card card--back">
    <div class="contact-layout">
      <div class="person">
        <p class="person__name">Marcus <span class="person__surname">Ellery</span></p>
        <p class="person__title">Managing Director</p>
      </div>
      <div class="divider"></div>
      <ul class="details">
        <li class="details__item">
          <svg class="details__icon" viewBox="0 0 24 24" aria-hidden="true"><path fill="#2fe3ee" d="M6.6 10.8a15.1 15.1 0 0 0 6.6 6.6l2.2-2.2a1 1 0 0 1 1-.25 11.4 11.4 0 0 0 3.6.57 1 1 0 0 1 1 1V20a1 1 0 0 1-1 1A17 17 0 0 1 3 4a1 1 0 0 1 1-1h3.5a1 1 0 0 1 1 1c0 1.25.2 2.45.57 3.57a1 1 0 0 1-.25 1z"/></svg>
          044-987 654 321
        </li>
        <li class="details__item">
          <svg class="details__icon" viewBox="0 0 24 24" aria-hidden="true"><rect x="2" y="5" width="20" height="14" fill="#2fe3ee"/><path d="M2 5l10 8 10-8" fill="none" stroke="#111112" stroke-width="1.8"/></svg>
          info@verodexmail.com
        </li>
        <li class="details__item">
          <svg class="details__icon" viewBox="0 0 24 24" aria-hidden="true"><g fill="none" stroke="#2fe3ee" stroke-width="2"><circle cx="12" cy="12" r="9.5"/><ellipse cx="12" cy="12" rx="4" ry="9.5"/><path d="M2.5 12h19M4 7h16M4 17h16"/></g></svg>
          www.verodexweb.com
        </li>
      </ul>
    </div>
    <div class="card__band"></div>
  </section>
</body>
</html>
```